Business Card Design

New business card design

Target Market(s)

Residential & Commercial Property Managers

Industry/Entity Type

Plumbing Services

Contact Information for Business Card

Name - Rowan Keddle, title - Director, Phone Number - 0431 286 517, email - rowan@tbk-plumbing.com.au, Company ABN - 73 215 904 386,

Font styles to use
Sans Serif

Colors
0054AA
0677BA
7BADD7
CADEEF
E8F1F8

```html
<!DOCTYPE html>
<html lang="en">
<head>
<meta charset="utf-8">
<title>TBK Plumbing Services – Business Card</title>
<link rel="stylesheet" href="https://fonts.googleapis.com/css2?family=Montserrat:wght@400;500;700&display=swap">
<style>
  :root {
    --stage: #2b2b2d;
    --sky: #29a8e0;
    --sky-light: #7bcbec;
    --ink: #1d232a;
    --paper: #ffffff;
    --accent: #2aa4dd;
    --tagline: #6a5e58;
  }
  * { box-sizing: border-box; margin: 0; padding: 0; }
  html, body {
    width: 1200px; height: 880px; overflow: hidden;
    background: var(--stage);
    font-family: "Montserrat", sans-serif;
  }
  .canvas { position: relative; width: 1200px; height: 880px; }
  .card {
    position: absolute; left: 240px; width: 720px; height: 411px;
    border-radius: 30px; overflow: hidden;
  }
  .card--front {
    top: 20px;
    background: linear-gradient(115deg, var(--sky) 0%, var(--sky-light) 30%, var(--sky) 60%, var(--sky) 100%);
  }
  .card--back { top: 449px; background: var(--paper); }

  .brand {
    position: absolute; display: flex; flex-direction: column; align-items: flex-start;
    font-weight: 500;
  }
  .brand__name {
    display: flex; align-items: center; gap: 18px;
    font-size: 120px; line-height: 1; letter-spacing: 4px; text-transform: lowercase;
  }
  .brand__dot { width: 26px; height: 26px; border-radius: 50%; background: currentColor; }
  .brand__tagline {
    font-size: 19px; letter-spacing: 14px; text-transform: lowercase; margin-top: 10px;
  }
  .card--front .brand { color: var(--paper); left: 150px; top: 110px; }
  .card--back .brand { color: var(--ink); left: 340px; top: 24px; }
  .card--back .brand__name { font-size: 84px; }
  .card--back .brand__dot { background: var(--accent); width: 20px; height: 20px; }
  .card--back .brand__tagline { font-size: 14px; letter-spacing: 10px; color: var(--tagline); margin-top: 6px; }

  .back-art { position: absolute; inset: 0; width: 720px; height: 411px; }

  .details { position: absolute; left: 0; top: 222px; color: var(--paper); }
  .details__marker {
    position: absolute; left: 42px; top: 8px; width: 14px; height: 60px; background: var(--accent);
  }
  .details__body { position: absolute; left: 70px; top: 0; width: 600px; }
  .details__name { color: var(--accent); font-weight: 700; font-size: 28px; line-height: 34px; }
  .details__title { font-size: 19px; line-height: 26px; }
  .details__abn { font-size: 18px; line-height: 24px; margin-top: 12px; }
  .details__contact { list-style: none; margin-top: 10px; font-size: 18px; line-height: 26px; }
  .details__contact li { display: flex; align-items: center; gap: 8px; }
  .details__contact svg { width: 16px; height: 16px; fill: var(--accent); }
</style>
</head>
<body>
<main class="canvas">
  <section class="card card--front">
    <div class="brand">
      <span class="brand__name">tbk <span class="brand__dot"></span></span>
      <span class="brand__tagline">plumbing services</span>
    </div>
  </section>

  <section class="card card--back">
    <svg class="back-art" viewBox="0 0 720 411" aria-hidden="true">
      <path d="M0,52 Q290,282 720,176" fill="none" stroke="var(--accent)" stroke-width="7"/>
      <path d="M0,70 Q280,300 720,190 L720,411 L0,411 Z" fill="var(--ink)"/>
    </svg>
    <div class="brand">
      <span class="brand__name">tbk <span class="brand__dot"></span></span>
      <span class="brand__tagline">plumbing services</span>
    </div>
    <div class="details">
      <span class="details__marker"></span>
      <div class="details__body">
        <p class="details__name">Rowan Keddle</p>
        <p class="details__title">Director</p>
        <p class="details__abn">Company ABN<br>- 73 215 904 386</p>
        <ul class="details__contact">
          <li>
            <svg viewBox="0 0 24 24"><path d="M6.6 10.8a15.1 15.1 0 0 0 6.6 6.6l2.2-2.2a1 1 0 0 1 1-.25 11.4 11.4 0 0 0 3.6.57 1 1 0 0 1 1 1V20a1 1 0 0 1-1 1A17 17 0 0 1 3 4a1 1 0 0 1 1-1h3.5a1 1 0 0 1 1 1c0 1.25.2 2.45.57 3.57a1 1 0 0 1-.25 1z"/></svg>
            0431 286 517
          </li>
          <li>
            <svg viewBox="0 0 24 24"><path d="M2 6h20v12H2z M2 6l10 7 10-7" fill="none" stroke="var(--accent)" stroke-width="2"/></svg>
            rowan@tbk-plumbing.com.au
          </li>
        </ul>
      </div>
    </div>
  </section>
</main>
</body>
</html>
```